Web Calculator design Housing Investment

We have a web calculator that needs to be fixed from a design perspective. The key tasks are:<br/>1. Selecting icons / pictures / colours for the various steps<br/>2. Designing navigation between calculator steps<br/>3. Making suggestions for chart design. The limitation is that the charts are all using the Vextra API (the same charts that Vextra Grids use).<br/><br/>There are four entry screens and then a result screen. See attached PDF for screenshots. You can see our website at https://larkhollowfunds.com for our corporate colours and style.

Target Market(s)

Real Estate Investors

Industry/Entity Type

Financial Planning

Number of Pages Required

1 page

Font styles to use
Sans Serif
Other font styles liked:
• Ubuntu

Colors
86cae7
3176b5
0455a3
ffffff

Requirements
Must have
• New Icons
• Suggested design for navigation
• Suggested design for charts

```html
<!DOCTYPE html>
<html lang="en">
<head>
<meta charset="utf-8">
<title>Housing Investment Calculator – Step Screens</title>
<link rel="stylesheet" href="https://fonts.googleapis.com/css2?family=Lato:wght@400;700&display=swap">
<style>
  :root {
    --sky: #86cae7;
    --mid-blue: #3176b5;
    --navy: #0455a3;
    --white: #ffffff;
    --stage: #242424;
    --panel: #f2f3f5;
    --card-edge: #e2e5e9;
    --ink: #222222;
    --muted: #555555;
    --grid: #e6e6e6;
    --track: #dcdcdc;
    --stat-bg: #f5f6f8;
    --note-bg: #eaf5fc;
    --note-edge: #cbe6f5;
    --grey-line: #8a8a8a;
  }
  html, body {
    margin: 0;
    width: 1200px;
    height: 575px;
    overflow: hidden;
    background: var(--stage);
    font-family: "Lato", sans-serif;
  }
  .board { position: relative; width: 1200px; height: 575px; }
  .screen { position: absolute; display: block; }
  .screen--type      { left: 89.4px;  top: 28.9px;  width: 325px; height: 199.6px; }
  .screen--location  { left: 439.3px; top: 28.9px;  width: 325px; height: 199.6px; }
  .screen--valuation { left: 788.6px; top: 28.9px;  width: 325px; height: 199.6px; }
  .screen--forecast  { left: 264.6px; top: 249.2px; width: 325px; height: 237.6px; }
  .screen--result    { left: 614.4px; top: 249.2px; width: 325px; height: 299.5px; }

  .panel-bg { fill: var(--panel); }
  .card { fill: var(--white); stroke: var(--card-edge); stroke-width: 2; }

  .step-track { stroke: var(--sky); stroke-width: 4; }
  .step-dot { stroke: var(--sky); stroke-width: 2.5; }
  .step-dot--done { fill: var(--navy); }
  .step-dot--todo { fill: var(--white); }
  .step-icon--done { color: var(--white); }
  .step-icon--todo { color: var(--mid-blue); }
  .step-label { fill: var(--navy); font-size: 9px; font-weight: 700; text-anchor: middle; }

  .question { fill: var(--ink); font-size: 11px; text-anchor: middle; }
  .heading { fill: var(--ink); font-size: 11px; font-weight: 700; text-anchor: middle; }
  .choice-ring { fill: var(--white); stroke: var(--mid-blue); stroke-width: 2.5; }
  .choice-title { fill: var(--mid-blue); font-size: 11px; font-weight: 700; text-anchor: middle; }
  .choice-copy { fill: var(--ink); font-size: 8.6px; text-anchor: middle; }

  .btn--primary { fill: var(--navy); }
  .btn--secondary { fill: var(--sky); }
  .btn-text { fill: var(--white); font-size: 8.6px; font-weight: 700; text-anchor: middle; letter-spacing: .3px; }

  .field-label { fill: var(--ink); font-size: 8.6px; }
  .field-value { fill: var(--ink); font-size: 8.2px; font-weight: 700; }
  .slider-track { stroke: var(--track); stroke-width: 2.5; stroke-linecap: round; }
  .slider-fill { stroke: var(--sky); stroke-width: 2.5; stroke-linecap: round; }
  .slider-knob { fill: var(--sky); stroke: var(--white); stroke-width: 1.5; }

  .body-copy { fill: var(--ink); font-size: 8.6px; }
  .select-box { fill: var(--white); stroke: var(--grid); stroke-width: 1; }
  .select-text { fill: var(--ink); font-size: 7.6px; }
  .select-caret { fill: var(--ink); }

  .axis-label { fill: var(--muted); font-size: 7.6px; }
  .grid-line { stroke: var(--grid); stroke-width: 1; }
  .axis-line { stroke: #cfcfcf; stroke-width: 1; }
  .series-yield { fill: none; stroke: var(--mid-blue); stroke-width: 1.6; }
  .series-shares { fill: none; stroke: var(--mid-blue); stroke-width: 1.6; }
  .series-property { fill: none; stroke: var(--grey-line); stroke-width: 1.6; }
  .series-nodebt { fill: none; stroke: var(--sky); stroke-width: 1.6; }
  .series-tag { fill: var(--navy); font-size: 7.6px; font-weight: 700; text-anchor: middle; }
  .bar-gain { fill: var(--sky); }
  .bar-cost { fill: var(--navy); }
  .legend-text { fill: var(--ink); font-size: 7.6px; }
  .legend-yield { fill: var(--navy); }
  .legend-forecast { fill: #3b95d9; }
  .caption { fill: var(--ink); font-size: 7.8px; text-anchor: middle; }

  .stat-card { fill: var(--stat-bg); stroke: var(--grid); stroke-width: 1; }
  .stat-title { fill: var(--navy); font-size: 11.5px; font-weight: 700; text-anchor: middle; }
  .stat-copy { fill: var(--muted); font-size: 7.8px; font-weight: 700; text-anchor: middle; }

  .note-box { fill: var(--note-bg); stroke: var(--note-edge); stroke-width: 1; }
  .note-text { fill: var(--muted); font-size: 7.4px; text-anchor: middle; }
  .advanced-box { fill: var(--white); stroke: var(--grid); stroke-width: 1; }
  .advanced-text { fill: var(--navy); font-size: 8px; }

  .info-dot { fill: #333333; }
  .info-i { fill: var(--white); font-size: 6px; font-weight: 700; text-anchor: middle; }
</style>
</head>
<body>
<svg width="0" height="0" style="position:absolute" aria-hidden="true">
  <defs>
    <symbol id="icon-home" viewBox="0 0 24 24"><path fill="currentColor" d="M12 3 2.5 11.5H6V20h4.5v-5h3v5H18v-8.5h3.5z"/></symbol>
    <symbol id="icon-pin" viewBox="0 0 24 24"><path fill="currentColor" fill-rule="evenodd" d="M12 2a7 7 0 0 0-7 7c0 5.2 7 13 7 13s7-7.8 7-13a7 7 0 0 0-7-7zm0 9.8a2.8 2.8 0 1 1 0-5.6 2.8 2.8 0 0 1 0 5.6z"/></symbol>
    <symbol id="icon-doc" viewBox="0 0 24 24"><path fill="currentColor" fill-rule="evenodd" d="M5.5 2h9l4.5 4.5V22H5.5zM8.5 10h7v1.6h-7zM8.5 13.5h7v1.6h-7zM8.5 17h7v1.6h-7z"/></symbol>
    <symbol id="icon-mic" viewBox="0 0 24 24"><rect x="9" y="2.5" width="6" height="12" rx="3" fill="currentColor"/><path d="M6.5 11a5.5 5.5 0 0 0 11 0M12 16.5V21M8.5 21h7" fill="none" stroke="currentColor" stroke-width="1.8"/></symbol>
    <symbol id="icon-calc" viewBox="0 0 24 24"><path fill="currentColor" fill-rule="evenodd" d="M5 2h14v20H5zM7.5 4.5h9v4h-9zM7.5 11h2.2v2.2H7.5zM10.9 11h2.2v2.2h-2.2zM14.3 11h2.2v2.2h-2.2zM7.5 14.6h2.2v2.2H7.5zM10.9 14.6h2.2v2.2h-2.2zM14.3 14.6h2.2v2.2h-2.2zM7.5 18.2h2.2v2.2H7.5zM10.9 18.2h2.2v2.2h-2.2zM14.3 18.2h2.2v2.2h-2.2z"/></symbol>
    <symbol id="icon-info" viewBox="0 0 10 10"><circle class="info-dot" cx="5" cy="5" r="5"/><rect x="4.3" y="4.2" width="1.4" height="3.8" fill="#fff"/><rect x="4.3" y="2" width="1.4" height="1.4" fill="#fff"/></symbol>
    <symbol id="caret" viewBox="0 0 6 10"><path class="select-caret" d="M3 0 6 4H0zM3 10 0 6h6z"/></symbol>
    <linearGradient id="soft-blue" x1="0" y1="0" x2="1" y2="1">
      <stop offset="0" stop-color="#86cae7"/><stop offset="1" stop-color="#3176b5"/>
    </linearGradient>
    <linearGradient id="warm-tones" x1="0" y1="0" x2="1" y2="1">
      <stop offset="0" stop-color="#f3c24a"/><stop offset="1" stop-color="#e9864a"/>
    </linearGradient>
  </defs>
</svg>

<main class="board">

  <!-- Step 1: property type -->
  <svg class="screen screen--type" viewBox="0 0 698 428" role="group" aria-label="Step 1, property type">
    <rect class="panel-bg" width="698" height="428"/>
    <rect class="card" x="36" y="33" width="627" height="385" rx="3"/>
    <g class="stepper">
      <line class="step-track" x1="86" y1="71" x2="614" y2="71"/>
      <circle class="step-dot step-dot--done" cx="86" cy="71" r="15"/><use href="#icon-home" class="step-icon--done" x="79" y="64" width="14" height="14"/>
      <circle class="step-dot step-dot--todo" cx="217" cy="71" r="15"/><use href="#icon-pin" class="step-icon--todo" x="210" y="64" width="14" height="14"/>
      <circle class="step-dot step-dot--todo" cx="349" cy="71" r="15"/><use href="#icon-doc" class="step-icon--todo" x="342" y="64" width="14" height="14"/>
      <circle class="step-dot step-dot--todo" cx="481" cy="71" r="15"/><use href="#icon-mic" class="step-icon--todo" x="474" y="64" width="14" height="14"/>
      <circle class="step-dot step-dot--todo" cx="614" cy="71" r="15"/><use href="#icon-calc" class="step-icon--todo" x="607" y="64" width="14" height="14"/>
      <text class="step-label" x="86" y="106">1. Property Type</text>
      <text class="step-label" x="217" y="106">2. Property Location</text>
      <text class="step-label" x="349" y="106">3. Property Valuation</text>
      <text class="step-label" x="481" y="106">4. YourProperty Forecast</text>
      <text class="step-label" x="614" y="106">5. Calculation</text>
    </g>
    <text class="question" x="349" y="156">What Type of Property would you like to compare?</text>
    <circle class="choice-ring" cx="270" cy="225" r="44"/>
    <rect x="245" y="200" width="50" height="50" rx="6" fill="url(#soft-blue)" role="img" aria-label="Illustration of a block of units"/>
    <text class="choice-title" x="270" y="296">Units</text>
    <circle class="choice-ring" cx="428" cy="225" r="44"/>
    <rect x="403" y="200" width="50" height="50" rx="6" fill="url(#soft-blue)" role="img" aria-label="Illustration of a house"/>
    <text class="choice-title" x="428" y="296">House</text>
    <rect class="btn--primary" x="304" y="345" width="89" height="29"/>
    <text class="btn-text" x="348.5" y="363">NEXT »</text>
  </svg>

  <!-- Step 2: location -->
  <svg class="screen screen--location" viewBox="0 0 698 428" role="group" aria-label="Step 2, property location">
    <rect class="panel-bg" width="698" height="428"/>
    <rect class="card" x="36" y="33" width="627" height="385" rx="3"/>
    <g class="stepper">
      <line class="step-track" x1="86" y1="71" x2="614" y2="71"/>
      <circle class="step-dot step-dot--done" cx="86" cy="71" r="15"/><use href="#icon-home" class="step-icon--done" x="79" y="64" width="14" height="14"/>
      <circle class="step-dot step-dot--done" cx="217" cy="71" r="15"/><use href="#icon-pin" class="step-icon--done" x="210" y="64" width="14" height="14"/>
      <circle class="step-dot step-dot--todo" cx="349" cy="71" r="15"/><use href="#icon-doc" class="step-icon--todo" x="342" y="64" width="14" height="14"/>
      <circle class="step-dot step-dot--todo" cx="481" cy="71" r="15"/><use href="#icon-mic" class="step-icon--todo" x="474" y="64" width="14" height="14"/>
      <circle class="step-dot step-dot--todo" cx="614" cy="71" r="15"/><use href="#icon-calc" class="step-icon--todo" x="607" y="64" width="14" height="14"/>
      <text class="step-label" x="86" y="106">1. Property Type</text>
      <text class="step-label" x="217" y="106">2. Property Location</text>
      <text class="step-label" x="349" y="106">3. Property Valuation</text>
      <text class="step-label" x="481" y="106">4. YourProperty Forecast</text>
      <text class="step-label" x="614" y="106">5. Calculation</text>
    </g>
    <text class="question" x="349" y="156">Where would this property be located ?</text>
    <rect x="172" y="170" width="156" height="144" rx="24" fill="url(#soft-blue)" role="img" aria-label="Selectable map of Australia divided into states"/>
    <text class="field-label" x="373" y="205">How much will the property cost?</text>
    <use href="#icon-info" x="526" y="198" width="8" height="8"/>
    <line class="slider-track" x1="375" y1="226" x2="577" y2="226"/>
    <line class="slider-fill" x1="375" y1="226" x2="419" y2="226"/>
    <circle class="slider-knob" cx="419" cy="226" r="5"/>
    <text class="field-value" x="583" y="229">$500, 000</text>
    <text class="field-label" x="373" y="252">How much will you invest?</text>
    <use href="#icon-info" x="493" y="245" width="8" height="8"/>
    <line class="slider-track" x1="375" y1="274" x2="577" y2="274"/>
    <line class="slider-fill" x1="375" y1="274" x2="404" y2="274"/>
    <circle class="slider-knob" cx="404" cy="274" r="5"/>
    <text class="field-value" x="583" y="277">$200, 000</text>
    <rect class="btn--secondary" x="253" y="345" width="88" height="29"/>
    <text class="btn-text" x="297" y="363">PREVIOUS »</text>
    <rect class="btn--primary" x="358" y="345" width="88" height="29"/>
    <text class="btn-text" x="402" y="363">NEXT »</text>
  </svg>

  <!-- Step 3: valuation method -->
  <svg class="screen screen--valuation" viewBox="0 0 698 428" role="group" aria-label="Step 3, property valuation">
    <rect class="panel-bg" width="698" height="428"/>
    <rect class="card" x="35" y="26" width="628" height="385" rx="3"/>
    <g class="stepper">
      <line class="step-track" x1="86" y1="71" x2="614" y2="71"/>
      <circle class="step-dot step-dot--done" cx="86" cy="71" r="15"/><use href="#icon-home" class="step-icon--done" x="79" y="64" width="14" height="14"/>
      <circle class="step-dot step-dot--done" cx="217" cy="71" r="15"/><use href="#icon-pin" class="step-icon--done" x="210" y="64" width="14" height="14"/>
      <circle class="step-dot step-dot--done" cx="349" cy="71" r="15"/><use href="#icon-doc" class="step-icon--done" x="342" y="64" width="14" height="14"/>
      <circle class="step-dot step-dot--todo" cx="481" cy="71" r="15"/><use href="#icon-mic" class="step-icon--todo" x="474" y="64" width="14" height="14"/>
      <circle class="step-dot step-dot--todo" cx="614" cy="71" r="15"/><use href="#icon-calc" class="step-icon--todo" x="607" y="64" width="14" height="14"/>
      <text class="step-label" x="86" y="106">1. Property Type</text>
      <text class="step-label" x="217" y="106">2. Property Location</text>
      <text class="step-label" x="349" y="106">3. Property Valuation</text>
      <text class="step-label" x="481" y="106">4. YourProperty Forecast</text>
      <text class="step-label" x="614" y="106">5. Calculation</text>
    </g>
    <text class="question" x="349" y="150">What Type of Property would you like to compare?</text>
    <circle class="choice-ring" cx="193" cy="219" r="44"/>
    <rect x="170" y="196" width="46" height="46" rx="6" fill="url(#warm-tones)" role="img" aria-label="Illustration of a calculator, bill and coin"/>
    <text class="choice-title" x="193" y="290">Relative Cost</text>
    <text class="choice-copy" x="193" y="312">Use this to value property based</text>
    <text class="choice-copy" x="193" y="326">on mortgage cost relative to</text>
    <text class="choice-copy" x="193" y="339">rent cost</text>
    <circle class="choice-ring" cx="349" cy="219" r="44"/>
    <rect x="326" y="196" width="46" height="46" rx="6" fill="url(#warm-tones)" role="img" aria-label="Illustration of a worker with a coin"/>
    <text class="choice-title" x="349" y="290">Relative to Wages</text>
    <text class="choice-copy" x="349" y="306">Use this to value property based</text>
    <text class="choice-copy" x="349" y="320">on mortgage cost relative</text>
    <text class="choice-copy" x="349" y="333">to wages</text>
    <circle class="choice-ring" cx="507" cy="219" r="44"/>
    <rect x="484" y="196" width="46" height="46" rx="23" fill="url(#warm-tones)" role="img" aria-label="Illustration of a percentage badge"/>
    <text class="choice-title" x="507" y="290">Using Rental Yield</text>
    <text class="choice-copy" x="507" y="306">Use this to value property based</text>
    <text class="choice-copy" x="507" y="320">on a rental yield</text>
    <rect class="btn--secondary" x="252" y="365" width="89" height="29"/>
    <text class="btn-text" x="296.5" y="383">PRIVIOUS »</text>
    <rect class="btn--primary" x="358" y="365" width="88" height="29"/>
    <text class="btn-text" x="402" y="383">NEXT »</text>
  </svg>

  <!-- Step 4: forecast -->
  <svg class="screen screen--forecast" viewBox="0 0 698 510" role="group" aria-label="Step 4, property price forecast">
    <rect class="panel-bg" width="698" height="510"/>
    <rect class="card" x="34" y="27" width="628" height="454" rx="3"/>
    <g class="stepper">
      <line class="step-track" x1="84" y1="71" x2="613" y2="71"/>
      <circle class="step-dot step-dot--done" cx="84" cy="71" r="15"/><use href="#icon-home" class="step-icon--done" x="77" y="64" width="14" height="14"/>
      <circle class="step-dot step-dot--done" cx="216" cy="71" r="15"/><use href="#icon-pin" class="step-icon--done" x="209" y="64" width="14" height="14"/>
      <circle class="step-dot step-dot--done" cx="348" cy="71" r="15"/><use href="#icon-doc" class="step-icon--done" x="341" y="64" width="14" height="14"/>
      <circle class="step-dot step-dot--done" cx="480" cy="71" r="15"/><use href="#icon-mic" class="step-icon--done" x="473" y="64" width="14" height="14"/>
      <circle class="step-dot step-dot--todo" cx="613" cy="71" r="15"/><use href="#icon-calc" class="step-icon--todo" x="606" y="64" width="14" height="14"/>
      <text class="step-label" x="84" y="105">1. Property Type</text>
      <text class="step-label" x="216" y="105">2. Property Location</text>
      <text class="step-label" x="348" y="105">3. Property Valuation</text>
      <text class="step-label" x="480" y="105">4. YourProperty Forecast</text>
      <text class="step-label" x="613" y="105">5. Calculation</text>
    </g>
    <text class="heading" x="347" y="150">Your Property Price Forecast</text>
    <text class="body-copy" x="433" y="178" text-anchor="end">You have chosen to forecast property prices using Gross Rental Yield</text>
    <rect class="select-box" x="442" y="164" width="112" height="22" rx="2"/>
    <text class="select-text" x="450" y="178">Gross Rental Yield</text>
    <use href="#caret" x="541" y="171" width="5" height="8"/>
    <text class="body-copy" x="490" y="209" text-anchor="end">You can see how this ratio has changed over time (in blue) below vs your assumption On red) for</text>
    <rect class="select-box" x="499" y="195" width="111" height="22" rx="2"/>
    <text class="select-text" x="507" y="209">Sydney House</text>
    <use href="#caret" x="597" y="202" width="5" height="8"/>

    <g class="yield-chart">
      <line class="grid-line" x1="148" y1="245" x2="550" y2="245"/>
      <line class="grid-line" x1="148" y1="285" x2="550" y2="285"/>
      <line class="grid-line" x1="148" y1="325" x2="550" y2="325"/>
      <line class="axis-line" x1="148" y1="364" x2="550" y2="364"/>
      <line class="axis-line" x1="148" y1="240" x2="148" y2="364"/>
      <text class="axis-label" x="140" y="248" text-anchor="end">15%</text>
      <text class="axis-label" x="140" y="288" text-anchor="end">10%</text>
      <text class="axis-label" x="140" y="328" text-anchor="end">5%</text>
      <text class="axis-label" x="140" y="367" text-anchor="end">0%</text>
      <text class="axis-label" x="174" y="383" text-anchor="middle">1985</text>
      <text class="axis-label" x="220" y="383" text-anchor="middle">1990</text>
      <text class="axis-label" x="266" y="383" text-anchor="middle">1995</text>
      <text class="axis-label" x="312" y="383" text-anchor="middle">2000</text>
      <text class="axis-label" x="357" y="383" text-anchor="middle">2005</text>
      <text class="axis-label" x="403" y="383" text-anchor="middle">2010</text>
      <text class="axis-label" x="449" y="383" text-anchor="middle">2015</text>
      <text class="axis-label" x="494" y="383" text-anchor="middle">2020</text>
      <text class="axis-label" x="540" y="383" text-anchor="middle">2025</text>
      <polyline class="series-yield" points="164,286 186,283 196,289 208,287 218,293 226,300 252,296 280,303 302,302 320,303 352,309 396,312 420,322 442,341 476,346 568,343"/>
    </g>
    <text class="caption" x="347" y="413">By default we assume the ratio stays at the latest value of 3.4%. You can change this assumption using the slider,</text>
    <line class="slider-track" x1="146" y1="431" x2="550" y2="431"/>
    <line class="slider-fill" x1="146" y1="431" x2="215" y2="431"/>
    <circle class="slider-knob" cx="215" cy="431" r="5.5"/>
    <rect class="legend-yield" x="279" y="453" width="8" height="8"/>
    <text class="legend-text" x="293" y="460">Gross Rental Yield</text>
    <rect class="legend-forecast" x="372" y="453" width="8" height="8"/>
    <text class="legend-text" x="385" y="460">Forecast</text>
  </svg>

  <!-- Step 5: calculation result -->
  <svg class="screen screen--result" viewBox="0 0 698 643" role="group" aria-label="Step 5, calculation">
    <rect class="panel-bg" width="698" height="643"/>
    <rect class="card" x="34" y="27" width="628" height="593" rx="3"/>
    <g class="stepper">
      <line class="step-track" x1="84" y1="71" x2="613" y2="71"/>
      <circle class="step-dot step-dot--done" cx="84" cy="71" r="15"/><use href="#icon-home" class="step-icon--done" x="77" y="64" width="14" height="14"/>
      <circle class="step-dot step-dot--done" cx="216" cy="71" r="15"/><use href="#icon-pin" class="step-icon--done" x="209" y="64" width="14" height="14"/>
      <circle class="step-dot step-dot--done" cx="348" cy="71" r="15"/><use href="#icon-doc" class="step-icon--done" x="341" y="64" width="14" height="14"/>
      <circle class="step-dot step-dot--done" cx="480" cy="71" r="15"/><use href="#icon-mic" class="step-icon--done" x="473" y="64" width="14" height="14"/>
      <circle class="step-dot step-dot--done" cx="613" cy="71" r="15"/><use href="#icon-calc" class="step-icon--done" x="606" y="64" width="14" height="14"/>
      <text class="step-label" x="84" y="105">1. Property Type</text>
      <text class="step-label" x="216" y="105">2. Property Location</text>
      <text class="step-label" x="348" y="105">3. Property Valuation</text>
      <text class="step-label" x="480" y="105">4. YourProperty Forecast</text>
      <text class="step-label" x="613" y="105">5. Calculation</text>
    </g>

    <text class="body-copy" x="191" y="152" text-anchor="end">Choose Property:</text>
    <rect class="select-box" x="198" y="138" width="111" height="22" rx="2"/>
    <text class="select-text" x="206" y="152">Sydney House</text>
    <use href="#caret" x="297" y="145" width="5" height="8"/>
    <text class="body-copy" x="460" y="152" text-anchor="end">Choose Alternative Investment:</text>
    <rect class="select-box" x="467" y="138" width="112" height="22" rx="2"/>
    <text class="select-text" x="475" y="152">Global Satus</text>
    <use href="#caret" x="567" y="145" width="5" height="8"/>

    <text class="body-copy" x="69" y="184">How much will the property cost?</text>
    <text class="body-copy" x="314" y="184" text-anchor="end">$500, 000</text>
    <line class="slider-track" x1="69" y1="203" x2="314" y2="203"/>
    <line class="slider-fill" x1="69" y1="203" x2="137" y2="203"/>
    <circle class="slider-knob" cx="137" cy="203" r="5.5"/>
    <text class="body-copy" x="383" y="184">How much will you invest?</text>
    <text class="body-copy" x="628" y="184" text-anchor="end">$200, 000</text>
    <line class="slider-track" x1="383" y1="203" x2="628" y2="203"/>
    <line class="slider-fill" x1="383" y1="203" x2="451" y2="203"/>
    <circle class="slider-knob" cx="451" cy="203" r="5.5"/>

    <g class="returns-chart">
      <line class="grid-line" x1="91" y1="238" x2="341" y2="238"/>
      <line class="grid-line" x1="91" y1="278" x2="341" y2="278"/>
      <line class="grid-line" x1="91" y1="318" x2="341" y2="318"/>
      <line class="axis-line" x1="91" y1="357" x2="341" y2="357"/>
      <line class="axis-line" x1="91" y1="234" x2="91" y2="357"/>
      <text class="axis-label" x="84" y="241" text-anchor="end">200K</text>
      <text class="axis-label" x="84" y="281" text-anchor="end">100K</text>
      <text class="axis-label" x="84" y="321" text-anchor="end">0</text>
      <text class="axis-label" x="84" y="360" text-anchor="end">-100K</text>
      <text class="axis-label" x="104" y="379" text-anchor="middle">2019</text>
      <text class="axis-label" x="150" y="379" text-anchor="middle">2021</text>
      <text class="axis-label" x="196" y="379" text-anchor="middle">2023</text>
      <text class="axis-label" x="242" y="379" text-anchor="middle">2025</text>
      <text class="axis-label" x="287" y="379" text-anchor="middle">2027</text>
      <text class="axis-label" x="333" y="379" text-anchor="middle">2029</text>
      <polyline class="series-nodebt" points="91,318 129,339 328,338"/>
      <polyline class="series-property" points="91,318 136,328 181,323 334,315"/>
      <polyline class="series-shares" points="91,318 176,311 341,275"/>
      <text class="series-tag" x="153" y="308">Shares</text>
      <text class="series-tag" x="197" y="327">Property</text>
      <text class="series-tag" x="292" y="311">Property if no debt</text>
    </g>

    <g class="contribution-chart">
      <line class="grid-line" x1="381" y1="238" x2="636" y2="238"/>
      <line class="grid-line" x1="381" y1="278" x2="636" y2="278"/>
      <line class="grid-line" x1="381" y1="318" x2="636" y2="318"/>
      <line class="axis-line" x1="381" y1="357" x2="636" y2="357"/>
      <line class="axis-line" x1="381" y1="234" x2="381" y2="357"/>
      <text class="axis-label" x="374" y="241" text-anchor="end">10K</text>
      <text class="axis-label" x="374" y="281" text-anchor="end">0</text>
      <text class="axis-label" x="374" y="321" text-anchor="end">-10K</text>
      <text class="axis-label" x="374" y="360" text-anchor="end">-20K</text>
      <text class="axis-label" x="394" y="379" text-anchor="middle">2019</text>
      <text class="axis-label" x="440" y="379" text-anchor="middle">2021</text>
      <text class="axis-label" x="486" y="379" text-anchor="middle">2023</text>
      <text class="axis-label" x="532" y="379" text-anchor="middle">2025</text>
      <text class="axis-label" x="578" y="379" text-anchor="middle">2027</text>
      <text class="axis-label" x="623" y="379" text-anchor="middle">2029</text>
      <rect class="bar-gain" x="401" y="277" width="12" height="1"/>
      <rect class="bar-cost" x="401" y="278" width="12" height="7"/>
      <rect class="bar-gain" x="425.5" y="275" width="12" height="3"/>
      <rect class="bar-cost" x="425.5" y="278" width="12" height="9"/>
      <rect class="bar-gain" x="450" y="273" width="12" height="5"/>
      <rect class="bar-cost" x="450" y="278" width="12" height="12"/>
      <rect class="bar-gain" x="474.5" y="271" width="12" height="7"/>
      <rect class="bar-cost" x="474.5" y="278" width="12" height="15"/>
      <rect class="bar-gain" x="499" y="269" width="12" height="9"/>
      <rect class="bar-cost" x="499" y="278" width="12" height="18"/>
      <rect class="bar-gain" x="523.5" y="268" width="12" height="10"/>
      <rect class="bar-cost" x="523.5" y="278" width="12" height="21"/>
      <rect class="bar-gain" x="548" y="266" width="12" height="12"/>
      <rect class="bar-cost" x="548" y="278" width="12" height="26"/>
      <rect class="bar-gain" x="572.5" y="265" width="12" height="13"/>
      <rect class="bar-cost" x="572.5" y="278" width="12" height="31"/>
      <rect class="bar-gain" x="597" y="263" width="12" height="15"/>
      <rect class="bar-cost" x="597" y="278" width="12" height="36"/>
      <rect class="bar-gain" x="621.5" y="260" width="12" height="18"/>
      <rect class="bar-cost" x="621.5" y="278" width="12" height="42"/>
    </g>

    <rect class="stat-card" x="69" y="404" width="174" height="60"/>
    <text class="stat-title" x="156" y="430">After 5 years</text>
    <text class="stat-copy" x="151" y="446">Shares will return $82,431 more</text>
    <use href="#icon-info" x="219" y="439" width="8" height="8"/>
    <rect class="stat-card" x="265" y="404" width="174" height="60"/>
    <text class="stat-title" x="352" y="430">After 10 years</text>
    <text class="stat-copy" x="347" y="446">Shares will return $160,176 more</text>
    <use href="#icon-info" x="418" y="439" width="8" height="8"/>
    <rect class="stat-card" x="460" y="404" width="174" height="60"/>
    <text class="stat-title" x="542" y="438">Debt Contribution</text>
    <use href="#icon-info" x="592" y="430" width="8" height="8"/>

    <rect class="btn--secondary" x="252" y="484" width="88" height="28"/>
    <text class="btn-text" x="296" y="501">PREVIOUS »</text>
    <rect class="btn--primary" x="357" y="484" width="88" height="28"/>
    <text class="btn-text" x="401" y="501">RECALCULATE »</text>

    <rect class="note-box" x="43" y="533" width="610" height="39"/>
    <text class="note-text" x="348" y="550">Note: These are indicative figures based on a broad range of assumptions (below). Please contact Larkhollow Funds or a financial planner before making any</text>
    <text class="note-text" x="348" y="562">investment based on the assumptions from this calculator.</text>
    <rect class="advanced-box" x="43" y="580" width="610" height="28"/>
    <text class="advanced-text" x="56" y="597">»&#160;&#160;&#160;Advanced Options</text>
  </svg>

</main>
</body>
</html>
```